Yard sign

Looking for a yard sign. <br/>Something simple, name, number. <br/>Large text, readable from 50 feet away. <br/><br/>18 x 24 inches.

Target Market(s)

Potential homeowners thinking about going solar.

Colors

Designer to choose colors to be used in the design.

Requirements
Must have
• "WE'VE GONE SOLAR!"
Nice to have
• We are a solar company, we would like a design that compliments the homeowners decision that they went solar and encourages others to do the same.

```html
<!DOCTYPE html>
<html lang="en">
<head>
<meta charset="utf-8">
<title>Sunvale Solar Yard Sign</title>
<link rel="stylesheet" href="https://fonts.googleapis.com/css2?family=Montserrat:wght@800&family=Roboto+Condensed:wght@700&family=Roboto:wght@700&display=swap">
<style>
  :root {
    --stage: #1a1617;
    --orange: #f7931e;
    --orange-deep: #f66522;
    --yellow: #fdc62a;
    --band: #da4104;
    --slate-light: #4a4a4a;
    --slate-dark: #262626;
    --white: #ffffff;
  }
  * { margin: 0; padding: 0; box-sizing: border-box; }
  html, body {
    width: 1200px; height: 1200px; overflow: hidden;
    background: var(--stage);
  }
  .sign {
    position: absolute; left: 214px; top: 78px;
    width: 774px; height: 1044px; overflow: hidden;
    background: radial-gradient(ellipse at 50% 52%, var(--slate-light) 0%, var(--slate-dark) 72%);
  }
  .sign-waves { position: absolute; inset: 0; width: 100%; height: 100%; }
  .brand {
    position: absolute; left: 60px; top: 238px; width: 660px;
    display: flex; align-items: center; gap: 32px;
  }
  .brand-dot {
    width: 150px; height: 150px; border-radius: 50%;
    background: var(--yellow); flex: none;
  }
  .brand-name {
    font-family: "Montserrat", sans-serif; font-weight: 800;
    font-size: 84px; line-height: 0.95; color: var(--orange);
    letter-spacing: -1px;
  }
  .slogan {
    position: absolute; left: 0; right: 0; top: 440px;
    text-align: center;
    font-family: "Roboto Condensed", sans-serif; font-weight: 700;
    font-size: 50px; line-height: 1; letter-spacing: 1px;
    color: var(--yellow);
  }
  .agent-name {
    position: absolute; left: 0; right: 0; top: 566px;
    text-align: center;
    font-family: "Roboto Condensed", sans-serif; font-weight: 700;
    font-size: 72px; line-height: 1; letter-spacing: -1.5px; color: var(--orange);
  }
  .phone-band {
    position: absolute; left: 0; right: 0; top: 649px; height: 114px;
    background: var(--band);
    display: flex; align-items: center; justify-content: center; gap: 14px;
  }
  .phone-icon { width: 80px; height: 80px; flex: none; }
  .phone-number {
    font-family: "Roboto Condensed", sans-serif; font-weight: 700;
    font-size: 104px; line-height: 1; color: var(--yellow);
    letter-spacing: 1px;
  }
  .web-address {
    position: absolute; left: 0; right: 0; top: 770px;
    text-align: center;
    font-family: "Roboto", sans-serif; font-weight: 700;
    font-size: 52px; line-height: 1.2; color: var(--yellow);
  }
</style>
</head>
<body>
  <main class="sign">
    <svg class="sign-waves" viewBox="0 0 774 1044" preserveAspectRatio="none" aria-hidden="true">
      <path d="M0 0 H774 V172 C300 60 120 70 0 107 Z" fill="var(--orange)"/>
      <path d="M391 0 H774 V125 C600 60 480 30 391 0 Z" fill="var(--orange-deep)"/>
      <path d="M0 107 C120 70 300 60 774 172 L774 203 C340 80 140 95 0 146 Z" fill="var(--yellow)"/>
      <path d="M0 821 C200 920 560 980 774 877 V1044 H0 Z" fill="var(--yellow)"/>
      <path d="M0 843 C200 945 560 1010 774 917 V1044 H0 Z" fill="var(--orange)"/>
      <path d="M0 896 Q220 960 407 1044 H0 Z" fill="var(--orange-deep)"/>
    </svg>

    <div class="brand">
      <span class="brand-dot"></span>
      <div class="brand-name">SUNVALE<br>SOLAR</div>
    </div>

    <p class="slogan">WE'VE GONE SOLAR!</p>

    <h1 class="agent-name">DANIEL MORENO</h1>

    <div class="phone-band">
      <svg class="phone-icon" viewBox="0 0 82 82" aria-hidden="true">
        <circle cx="41" cy="41" r="38" fill="var(--band)" stroke="var(--yellow)" stroke-width="4"/>
        <circle cx="41" cy="41" r="33" fill="var(--band)" stroke="var(--white)" stroke-width="2"/>
        <path d="M25 26 q4-4 8 0 l4 6 q1 3-2 5 l-2 2 q3 7 10 11 l2-2 q2-3 5-1 l6 4 q3 3 0 7 l-3 3 q-5 3-14-3 q-11-8-16-19 q-3-8 2-13 Z" fill="var(--white)"/>
        <path d="M44 28 q8 1 10 9" fill="none" stroke="var(--white)" stroke-width="2.5" stroke-linecap="round"/>
        <path d="M45 21 q14 2 16 16" fill="none" stroke="var(--white)" stroke-width="2.5" stroke-linecap="round"/>
      </svg>
      <span class="phone-number">555-014-2876</span>
    </div>

    <p class="web-address">www.sunvale.net</p>
  </main>
</body>
</html>
```